showcase project portfolio

create power point of project portfolio
from word file and website using similar design template

https://www.brelmor.co.uk/

Target Market(s)

corporte

```html
<!DOCTYPE html>
<html lang="en">
<head>
<meta charset="utf-8">
<title>Brelmor Design Solutions – Project Portfolio</title>
<link href="https://fonts.googleapis.com/css2?family=Montserrat:wght@600;700&family=Questrial&display=swap" rel="stylesheet">
<style>
:root{
  --navy:#1f3a52;
  --navy-deep:#183047;
  --tan:#c9a27e;
  --tan-light:#dcbfa3;
  --panel:#f4f4f5;
  --canvas:#cbc8cb;
  --ink:#1d2a36;
  --white:#ffffff;
  --photo:linear-gradient(180deg,#e1e5ea 0%,#cfcdcf 32%,#a98e85 52%,#8f7b76 72%,#6c6d72 100%);
}
*{margin:0;padding:0;box-sizing:border-box}
html,body{width:1200px;height:2469px;overflow:hidden}
body{position:relative;background:var(--canvas);font-family:"Questrial",sans-serif;color:var(--ink)}
.hero{position:absolute;left:0;top:0;width:1200px;height:750px;background:linear-gradient(180deg,#d9dde3 0%,#e8eaee 100%)}
.hero .slide{left:150px;top:120px;transform:scale(1.6);transform-origin:0 0;box-shadow:0 10px 30px rgba(0,0,0,.18)}
.slide{position:absolute;width:562px;height:316px;overflow:hidden;background:var(--white)}
.abs{position:absolute}
.photo{position:absolute;background:var(--photo)}
.plan{position:absolute;background:linear-gradient(135deg,#ffffff 0%,#f1f1ee 60%,#e7e6df 100%);border:1px solid #cfd3d8}
.plan.colour{background:linear-gradient(135deg,#fbf6d8 0%,#f3f0c8 50%,#e9eef2 100%)}
.greenery{background:linear-gradient(180deg,#7d8b70 0%,#5d6e4f 50%,#807a72 100%)}
.brick{background:linear-gradient(180deg,#8d5b47 0%,#a3644c 55%,#e6e3df 80%,#d9d6d2 100%)}
.house{background:linear-gradient(180deg,#aeb6c0 0%,#4d4d52 40%,#e6e1da 70%,#7b6f66 100%)}
.logo{position:absolute;display:flex;align-items:center;gap:5px;font-family:"Montserrat",sans-serif;font-weight:700;color:var(--navy);letter-spacing:.3px}
.logo .mark{width:9px;height:9px;background:var(--tan)}
.logo.light{color:var(--white)}
.title{position:absolute;font-family:"Montserrat",sans-serif;font-weight:700;font-size:29px;line-height:34px;color:var(--navy)}
.subtitle{position:absolute;font-size:15px;color:var(--navy)}
.date{position:absolute;font-size:6.5px;color:var(--navy)}
.on-dark{color:var(--white)}
.band{position:absolute;left:0;bottom:0;width:100%;height:24px;display:flex;align-items:center;justify-content:center;font-size:5.5px;color:var(--white)}
.band.gradient{background:linear-gradient(90deg,var(--navy) 0%,var(--navy) 45%,var(--tan) 100%)}
.band.plain{background:var(--white);color:var(--navy)}
.band.tan{background:var(--tan);color:var(--navy)}
/* tasks */
.tasks-head{position:absolute;left:50px;top:40px;font-family:"Montserrat",sans-serif;font-weight:700;font-size:16px;color:var(--navy);letter-spacing:.5px}
.tasks-rule{position:absolute;left:50px;top:64px;width:48px;height:5px;border-radius:3px;background:linear-gradient(90deg,var(--tan),var(--tan-light))}
.tasks-band{position:absolute;left:0;top:100px;width:460px;height:150px;background:linear-gradient(90deg,var(--navy) 0%,rgba(31,58,82,.92) 45%,rgba(201,162,126,.9) 100%)}
.tasks-list{position:absolute;top:14px;list-style:none;width:175px}
.tasks-list li{position:relative;padding-left:12px;font-size:6.4px;font-style:italic;line-height:7.2px;color:var(--white);margin-bottom:6px}
.tasks-list li::before{content:"";position:absolute;left:2px;top:2.5px;width:2.5px;height:2.5px;background:var(--white)}
/* projects */
.left-panel{position:absolute;left:0;top:0;width:218px;height:316px;background:var(--panel)}
.right-panel{position:absolute;left:218px;top:0;width:344px;height:316px;background:var(--navy)}
.tab{position:absolute;left:0;top:25px;width:230px;height:30px;background:linear-gradient(90deg,var(--navy) 0%,var(--navy) 40%,var(--tan) 100%);font-family:"Montserrat",sans-serif;font-weight:700;font-size:15px;color:var(--white);padding:6px 0 0 30px;letter-spacing:.3px}
.info{position:absolute;left:14px;width:190px;text-align:center}
.icon{display:block;margin:0 auto 3px}
.label{font-size:10px;color:var(--tan)}
.label.dark{color:var(--navy)}
.address{font-family:"Montserrat",sans-serif;font-weight:600;font-size:8px;line-height:9.5px;color:var(--ink);margin-top:5px}
.proposal{font-size:6.8px;line-height:7.8px;font-style:italic;color:var(--ink);margin-top:6px}
.foot-note{position:absolute;right:32px;bottom:16px;font-size:5.2px;color:var(--white)}
.page{position:absolute;right:14px;bottom:15px;width:9px;height:9px;border-radius:2px;background:var(--tan);font-size:5px;color:var(--white);text-align:center;line-height:9px}
/* contact */
.contact-head{position:absolute;left:62px;top:140px;font-family:"Montserrat",sans-serif;font-weight:700;font-size:10px;color:var(--white);letter-spacing:.6px}
.contact-address{position:absolute;left:62px;top:160px;font-size:7px;line-height:8.5px;color:var(--white)}
.contact-list{position:absolute;left:62px;top:192px;list-style:none}
.contact-list li{display:flex;align-items:center;gap:7px;font-size:7px;color:var(--white);margin-bottom:6px}
</style>
</head>
<body>

<section class="hero" aria-label="Cover">
  <div class="slide cover-light">
    <div class="photo" role="img" aria-label="Street photo of a brick corner building" style="inset:0"></div>
    <div class="abs" style="inset:0;background:linear-gradient(90deg,#fff 0%,rgba(255,255,255,.93) 28%,rgba(255,255,255,.45) 62%,rgba(255,255,255,.2) 100%)"></div>
    <div class="logo" style="left:55px;top:70px;font-size:14px"><span class="mark"></span>brelmor</div>
    <div class="title" style="left:55px;top:128px">Brelmor Design<br>Solutions</div>
    <div class="subtitle" style="left:55px;top:200px">Project Portfolio</div>
    <div class="date" style="left:55px;top:228px">Tuesday, June 4, 2024</div>
    <div class="band gradient">© 2024 Brelmor Design Solutions. All rights reserved.</div>
  </div>
</section>

<!-- Row 1 -->
<div class="slide cover-light" style="left:28px;top:778px">
  <div class="photo" role="img" aria-label="Street photo of a brick corner building" style="inset:0"></div>
  <div class="abs" style="inset:0;background:linear-gradient(90deg,#fff 0%,rgba(255,255,255,.93) 28%,rgba(255,255,255,.45) 62%,rgba(255,255,255,.2) 100%)"></div>
  <div class="logo" style="left:55px;top:70px;font-size:14px"><span class="mark"></span>brelmor</div>
  <div class="title" style="left:55px;top:128px">Brelmor Design<br>Solutions</div>
  <div class="subtitle" style="left:55px;top:200px">Project Portfolio</div>
  <div class="date" style="left:55px;top:228px">Tuesday, June 4, 2024</div>
  <div class="band gradient">© 2024 Brelmor Design Solutions. All rights reserved.</div>
</div>

<div class="slide cover-dark" style="left:609px;top:778px">
  <div class="photo" role="img" aria-label="Street photo of a brick corner building" style="inset:0"></div>
  <div class="abs" style="inset:0;background:linear-gradient(90deg,var(--navy) 0%,rgba(31,58,82,.92) 32%,rgba(31,58,82,.45) 66%,rgba(31,58,82,.2) 100%)"></div>
  <div class="logo light" style="left:55px;top:70px;font-size:14px"><span class="mark"></span>brelmor</div>
  <div class="title on-dark" style="left:55px;top:128px">Brelmor Design<br>Solutions</div>
  <div class="subtitle on-dark" style="left:55px;top:200px">Project Portfolio</div>
  <div class="date on-dark" style="left:55px;top:228px">Tuesday, June 4, 2024</div>
  <div class="band plain">© 2024 Brelmor Design Solutions. All rights reserved.</div>
</div>

<!-- Row 2 -->
<div class="slide tasks" style="left:28px;top:1113px">
  <div class="photo" role="img" aria-label="Street photo of a brick corner building" style="left:350px;top:0;width:212px;height:316px"></div>
  <div class="tasks-head">TASKS</div>
  <div class="tasks-rule"></div>
  <div class="tasks-band">
    <ul class="tasks-list" style="left:50px">
      <li>Creating working drawings</li>
      <li>Price breakdown of total build costs</li>
      <li>Liaising with Midshire Water for water connection, drainage connection</li>
      <li>Liaising with Northvale Gas to get gas supply to site</li>
      <li>Liaising with Graystone Grid to get electric supply</li>
      <li>Tendering out works to different tradesman</li>
      <li>Getting material orders</li>
    </ul>
    <ul class="tasks-list" style="left:240px">
      <li>Arranging structural engineer for the site</li>
      <li>Arranging Building control for the site</li>
      <li>Making sure material is on site on time</li>
      <li>Making sure all tradesman work is up to current British standards</li>
      <li>Daily walk rounds to check work is done according to approved plans</li>
      <li>Placing orders for bathrooms, kitchen, and flooring</li>
      <li>All snag work with main contactor</li>
    </ul>
  </div>
  <div class="logo" style="left:16px;top:282px;font-size:9px"><span class="mark" style="width:6px;height:6px"></span>brelmor</div>
  <div class="foot-note">© 2024 Brelmor Design Solutions. All rights reserved.</div>
  <div class="page">3</div>
</div>

<div class="slide project" style="left:609px;top:1113px">
  <div class="left-panel"></div>
  <div class="right-panel"></div>
  <div class="tab">PROJECT: 1</div>
  <div class="info" style="top:70px">
    <svg class="icon" width="32" height="32" viewBox="0 0 32 32"><circle cx="16" cy="16" r="16" fill="var(--tan)"/><path d="M16 8a5.5 5.5 0 0 0-5.5 5.5c0 4.2 5.5 10.5 5.5 10.5s5.5-6.3 5.5-10.5A5.5 5.5 0 0 0 16 8z" fill="none" stroke="#fff" stroke-width="1.6"/><circle cx="16" cy="13.5" r="2" fill="#fff"/></svg>
    <div class="label">Location</div>
    <div class="address">Garages at Fernlea Mews,<br>Fernlea Street, Derby</div>
  </div>
  <div class="info" style="top:158px">
    <svg class="icon" width="32" height="32" viewBox="0 0 32 32"><circle cx="16" cy="16" r="16" fill="var(--navy)"/><path d="M16 8.5a5 5 0 0 0-3 9v2.5h6v-2.5a5 5 0 0 0-3-9z" fill="none" stroke="#fff" stroke-width="1.5"/><path d="M13.5 22h5M14.5 24h3" stroke="#fff" stroke-width="1.4"/></svg>
    <div class="label">Proposal</div>
    <div class="proposal">Change of use from garages to two dwelling houses (use class C3) including alterations to the front and side elevations</div>
  </div>
  <div class="logo" style="left:16px;top:282px;font-size:9px"><span class="mark" style="width:6px;height:6px"></span>brelmor</div>
  <div class="photo greenery" role="img" aria-label="Photo of the garage block along the mews" style="left:244px;top:26px;width:182px;height:92px"></div>
  <div class="plan colour" role="img" aria-label="Floor plan drawings for the two dwellings" style="left:432px;top:26px;width:105px;height:92px"></div>
  <div class="photo brick" role="img" aria-label="Photo of the converted brick dwellings" style="left:244px;top:124px;width:293px;height:152px"></div>
  <div class="foot-note">© 2024 Brelmor Design Solutions. All rights reserved.</div>
  <div class="page">4</div>
</div>

<!-- Row 3 -->
<div class="slide project" style="left:28px;top:1448px">
  <div class="left-panel"></div>
  <div class="right-panel"></div>
  <div class="tab">PROJECT: 2</div>
  <div class="info" style="top:70px">
    <svg class="icon" width="32" height="32" viewBox="0 0 32 32"><circle cx="16" cy="16" r="16" fill="var(--tan)"/><path d="M16 8a5.5 5.5 0 0 0-5.5 5.5c0 4.2 5.5 10.5 5.5 10.5s5.5-6.3 5.5-10.5A5.5 5.5 0 0 0 16 8z" fill="none" stroke="#fff" stroke-width="1.6"/><circle cx="16" cy="13.5" r="2" fill="#fff"/></svg>
    <div class="label">Location</div>
    <div class="address">118 Holloway Road,<br>Derby</div>
  </div>
  <div class="info" style="top:158px">
    <svg class="icon" width="32" height="32" viewBox="0 0 32 32"><circle cx="16" cy="16" r="16" fill="var(--navy)"/><path d="M16 8.5a5 5 0 0 0-3 9v2.5h6v-2.5a5 5 0 0 0-3-9z" fill="none" stroke="#fff" stroke-width="1.5"/><path d="M13.5 22h5M14.5 24h3" stroke="#fff" stroke-width="1.4"/></svg>
    <div class="label">Proposal</div>
    <div class="proposal">Change of use from offices (use class B1)<br>to 12 flats (use class C3)</div>
  </div>
  <div class="logo" style="left:16px;top:282px;font-size:9px"><span class="mark" style="width:6px;height:6px"></span>brelmor</div>
  <div class="photo greenery" role="img" aria-label="Photo of the office building behind trees" style="left:244px;top:26px;width:144px;height:90px"></div>
  <div class="photo greenery" role="img" aria-label="Photo of the building entrance and driveway" style="left:394px;top:26px;width:143px;height:90px"></div>
  <div class="plan" role="img" aria-label="Floor plan drawings for the twelve flats" style="left:244px;top:122px;width:293px;height:154px"></div>
  <div class="foot-note">© 2024 Brelmor Design Solutions. All rights reserved.</div>
  <div class="page">5</div>
</div>

<div class="slide project" style="left:609px;top:1448px">
  <div class="left-panel"></div>
  <div class="right-panel"></div>
  <div class="tab">PROJECT: 3</div>
  <div class="info" style="top:70px">
    <svg class="icon" width="32" height="32" viewBox="0 0 32 32"><circle cx="16" cy="16" r="16" fill="var(--tan)"/><path d="M16 8a5.5 5.5 0 0 0-5.5 5.5c0 4.2 5.5 10.5 5.5 10.5s5.5-6.3 5.5-10.5A5.5 5.5 0 0 0 16 8z" fill="none" stroke="#fff" stroke-width="1.6"/><circle cx="16" cy="13.5" r="2" fill="#fff"/></svg>
    <div class="label">Location</div>
    <div class="address">71-75 Queen Lane,<br>Derby</div>
  </div>
  <div class="info" style="top:158px">
    <svg class="icon" width="32" height="32" viewBox="0 0 32 32"><circle cx="16" cy="16" r="16" fill="var(--navy)"/><path d="M16 8.5a5 5 0 0 0-3 9v2.5h6v-2.5a5 5 0 0 0-3-9z" fill="none" stroke="#fff" stroke-width="1.5"/><path d="M13.5 22h5M14.5 24h3" stroke="#fff" stroke-width="1.4"/></svg>
    <div class="label">Proposal</div>
    <div class="proposal" style="font-size:6.4px;line-height:7.2px">Refurbishment Of Commercial Ground Floor Units Together With Formation Of 6 Residential Units On First And Second Floors. Installation Of Glazing And Repair To External Masonry Including Bricking Up Of Existing Openings</div>
  </div>
  <div class="logo" style="left:16px;top:282px;font-size:9px"><span class="mark" style="width:6px;height:6px"></span>brelmor</div>
  <div class="photo house" role="img" aria-label="Photo of the gable end of the terrace" style="left:244px;top:26px;width:144px;height:118px"></div>
  <div class="photo house" role="img" aria-label="Photo of the street frontage" style="left:394px;top:26px;width:143px;height:118px"></div>
  <div class="plan colour" role="img" aria-label="Ground floor plan" style="left:244px;top:150px;width:94px;height:126px"></div>
  <div class="plan colour" role="img" aria-label="First floor plan" style="left:343px;top:150px;width:94px;height:126px"></div>
  <div class="plan colour" role="img" aria-label="Second floor plan" style="left:442px;top:150px;width:95px;height:126px"></div>
  <div class="foot-note">© 2024 Brelmor Design Solutions. All rights reserved.</div>
  <div class="page">6</div>
</div>

<!-- Row 4 -->
<div class="slide project" style="left:28px;top:1783px">
  <div class="left-panel"></div>
  <div class="right-panel"></div>
  <div class="tab">PROJECT: 4</div>
  <div class="info" style="top:70px">
    <svg class="icon" width="32" height="32" viewBox="0 0 32 32"><circle cx="16" cy="16" r="16" fill="var(--tan)"/><path d="M16 8a5.5 5.5 0 0 0-5.5 5.5c0 4.2 5.5 10.5 5.5 10.5s5.5-6.3 5.5-10.5A5.5 5.5 0 0 0 16 8z" fill="none" stroke="#fff" stroke-width="1.6"/><circle cx="16" cy="13.5" r="2" fill="#fff"/></svg>
    <div class="label">Location</div>
    <div class="address">Land At 3 Elmfield,<br>Derby DE23 9ZZ</div>
  </div>
  <div class="info" style="top:158px">
    <svg class="icon" width="32" height="32" viewBox="0 0 32 32"><circle cx="16" cy="16" r="16" fill="var(--navy)"/><path d="M16 8.5a5 5 0 0 0-3 9v2.5h6v-2.5a5 5 0 0 0-3-9z" fill="none" stroke="#fff" stroke-width="1.5"/><path d="M13.5 22h5M14.5 24h3" stroke="#fff" stroke-width="1.4"/></svg>
    <div class="label">Proposal</div>
    <div class="proposal">Erection of a dwelling house (use class C3)</div>
  </div>
  <div class="logo" style="left:16px;top:282px;font-size:9px"><span class="mark" style="width:6px;height:6px"></span>brelmor</div>
  <div class="plan colour" role="img" aria-label="Site and floor plans for the new dwelling" style="left:244px;top:26px;width:144px;height:150px"></div>
  <div class="plan" role="img" aria-label="Proposed front elevation drawing" style="left:244px;top:182px;width:144px;height:94px"></div>
  <div class="photo greenery" role="img" aria-label="Photo of the overgrown plot" style="left:394px;top:26px;width:143px;height:86px"></div>
  <div class="photo house" role="img" aria-label="Photo of the completed detached house" style="left:394px;top:118px;width:143px;height:158px"></div>
  <div class="foot-note">© 2024 Brelmor Design Solutions. All rights reserved.</div>
  <div class="page">7</div>
</div>

<div class="slide project" style="left:609px;top:1783px">
  <div class="left-panel"></div>
  <div class="right-panel"></div>
  <div class="tab">PROJECT: 5</div>
  <div class="info" style="top:70px">
    <svg class="icon" width="32" height="32" viewBox="0 0 32 32"><circle cx="16" cy="16" r="16" fill="var(--tan)"/><path d="M16 8a5.5 5.5 0 0 0-5.5 5.5c0 4.2 5.5 10.5 5.5 10.5s5.5-6.3 5.5-10.5A5.5 5.5 0 0 0 16 8z" fill="none" stroke="#fff" stroke-width="1.6"/><circle cx="16" cy="13.5" r="2" fill="#fff"/></svg>
    <div class="label">Location</div>
    <div class="address">14, Carver Row,<br>Birmingham</div>
  </div>
  <div class="info" style="top:158px">
    <svg class="icon" width="32" height="32" viewBox="0 0 32 32"><circle cx="16" cy="16" r="16" fill="var(--navy)"/><path d="M16 8.5a5 5 0 0 0-3 9v2.5h6v-2.5a5 5 0 0 0-3-9z" fill="none" stroke="#fff" stroke-width="1.5"/><path d="M13.5 22h5M14.5 24h3" stroke="#fff" stroke-width="1.4"/></svg>
    <div class="label">Proposal</div>
    <div class="proposal">Warehouse conversion to 4 town houses.</div>
  </div>
  <div class="logo" style="left:16px;top:282px;font-size:9px"><span class="mark" style="width:6px;height:6px"></span>brelmor</div>
  <div class="photo brick" role="img" aria-label="Photo of the warehouse frontage" style="left:244px;top:26px;width:82px;height:92px"></div>
  <div class="photo" role="img" aria-label="Photo of the rear courtyard" style="left:332px;top:26px;width:82px;height:92px;background:linear-gradient(180deg,#8fb0d8 0%,#9a6a56 45%,#7d5a4c 100%)"></div>
  <div class="plan" role="img" aria-label="Floor plan drawings for the town houses" style="left:420px;top:26px;width:117px;height:92px"></div>
  <div class="photo brick" role="img" aria-label="Photo of the arched warehouse windows" style="left:244px;top:124px;width:293px;height:152px"></div>
  <div class="foot-note">© 2024 Brelmor Design Solutions. All rights reserved.</div>
  <div class="page">8</div>
</div>

<!-- Row 5 -->
<div class="slide contact" style="left:28px;top:2118px">
  <div class="photo" role="img" aria-label="Street photo of a brick corner building" style="inset:0"></div>
  <div class="abs" style="inset:0;background:linear-gradient(90deg,rgba(31,58,82,.92) 0%,rgba(31,58,82,.75) 40%,rgba(31,58,82,.35) 100%)"></div>
  <div class="logo light" style="left:62px;top:80px;font-size:14px"><span class="mark"></span>brelmor</div>
  <div class="contact-head">CONTACT US</div>
  <div class="contact-address">Unit 4 Riverside Court, Allestree,<br>Derby DE22 9ZZ</div>
  <ul class="contact-list">
    <li><svg width="9" height="9" viewBox="0 0 24 24"><path d="M6.6 10.8a15 15 0 0 0 6.6 6.6l2.2-2.2c.3-.3.7-.4 1-.2 1.1.4 2.3.6 3.6.6.6 0 1 .4 1 1V20c0 .6-.4 1-1 1A17 17 0 0 1 3 4c0-.6.4-1 1-1h3.5c.6 0 1 .4 1 1 0 1.3.2 2.5.6 3.6.1.3 0 .7-.2 1z" fill="#fff"/></svg>+44 7700 900415</li>
    <li><svg width="9" height="9" viewBox="0 0 24 24"><circle cx="12" cy="12" r="4" fill="none" stroke="#fff" stroke-width="2.4"/><path d="M16 8v5.5a2.5 2.5 0 0 0 5 0V12a9 9 0 1 0-3.5 7.1" fill="none" stroke="#fff" stroke-width="2.4"/></svg>info@brelmor.co.uk</li>
    <li><svg width="9" height="9" viewBox="0 0 24 24"><circle cx="12" cy="12" r="10" fill="none" stroke="#fff" stroke-width="2"/><path d="M2 12h20M12 2c3 3 3 17 0 20M12 2c-3 3-3 17 0 20" fill="none" stroke="#fff" stroke-width="1.6"/></svg>www.brelmor.co.uk</li>
  </ul>
  <div class="band tan">© 2024 Brelmor Design Solutions. All rights reserved.</div>
</div>

<div class="slide contact" style="left:609px;top:2118px">
  <div class="photo" role="img" aria-label="Street photo of a brick corner building" style="inset:0"></div>
  <div class="abs" style="inset:0;background:linear-gradient(90deg,rgba(31,58,82,.92) 0%,rgba(31,58,82,.75) 40%,rgba(31,58,82,.35) 100%)"></div>
  <div class="logo light" style="left:62px;top:80px;font-size:14px"><span class="mark"></span>brelmor</div>
  <div class="contact-head">CONTACT US</div>
  <div class="contact-address">Unit 4 Riverside Court, Allestree,<br>Derby DE22 9ZZ</div>
  <ul class="contact-list">
    <li><svg width="9" height="9" viewBox="0 0 24 24"><path d="M6.6 10.8a15 15 0 0 0 6.6 6.6l2.2-2.2c.3-.3.7-.4 1-.2 1.1.4 2.3.6 3.6.6.6 0 1 .4 1 1V20c0 .6-.4 1-1 1A17 17 0 0 1 3 4c0-.6.4-1 1-1h3.5c.6 0 1 .4 1 1 0 1.3.2 2.5.6 3.6.1.3 0 .7-.2 1z" fill="#fff"/></svg>+44 7700 900415</li>
    <li><svg width="9" height="9" viewBox="0 0 24 24"><circle cx="12" cy="12" r="4" fill="none" stroke="#fff" stroke-width="2.4"/><path d="M16 8v5.5a2.5 2.5 0 0 0 5 0V12a9 9 0 1 0-3.5 7.1" fill="none" stroke="#fff" stroke-width="2.4"/></svg>info@brelmor.co.uk</li>
    <li><svg width="9" height="9" viewBox="0 0 24 24"><circle cx="12" cy="12" r="10" fill="none" stroke="#fff" stroke-width="2"/><path d="M2 12h20M12 2c3 3 3 17 0 20M12 2c-3 3-3 17 0 20" fill="none" stroke="#fff" stroke-width="1.6"/></svg>www.brelmor.co.uk</li>
  </ul>
  <div class="band plain">© 2024 Brelmor Design Solutions. All rights reserved.</div>
</div>

</body>
</html>
```